UK landscaping company needs website

We, Brackwell Landscapes need a website design for a company based in Surrey, UK. The design should be bold and playful. We have three main areas of work driveways, paving and fencing. It shouldn't be too heavy in text and concentrate on the pictures from previous jobs we've completed. You may use stock images for the design, these can be changed if you are successful. Please don’t just copy the flyer it is just there to provide content.
We have a logo design which we would also like editing slightly.
Here are some of my local competitors
https://www.pelmarlandscapes.example.co.uk/

https://www.twinfirgardendesign.example.com/

https://kestbyrnlandscapes.example.co.uk/

Industry/Entity Type

Landscaping

Coding

Coded - Design and coding required

Number of Pages Required

3 page

Font styles to use
Sans Serif

Requirements
Must have
• Pictures of my previous jobs.
Must be mobile friendly
Easy to navigate
Nice to have
• Try to use different colours. It would be good to have some designs that aren’t just black and green.
I’d like some curves in the design.
Should not have
• We install hard landscaping. Think more building/construction and less plants and cutting grass.

```html
<!DOCTYPE html>
<html lang="en">
<head>
<meta charset="utf-8">
<title>Brackwell Landscapes</title>
<link rel="stylesheet" href="https://fonts.googleapis.com/css2?family=Montserrat:wght@400;500;600&display=swap">
<style>
:root{
  --green:#5cb531;
  --green-dark:#3f8f1f;
  --black:#000;
  --white:#fff;
  --ink:#222;
  --grey-text:#555;
  --soft:#f4f4f4;
  --dark:#1d1c1a;
  --star:#e8a317;
}
*{box-sizing:border-box;margin:0;padding:0}
html,body{width:1200px;height:3533px;overflow:hidden}
body{position:relative;font-family:Arial,Helvetica,sans-serif;color:var(--ink);background:var(--white)}

/* header */
.site-header{position:absolute;left:0;top:0;width:1200px;height:120px;background:var(--black);border-bottom:2px solid var(--white)}
.brand{position:absolute;left:111px;top:48px;display:flex;align-items:center;gap:10px;color:var(--white);font-family:'Montserrat',sans-serif;font-weight:600;font-size:18px;line-height:22px;letter-spacing:.3px;white-space:nowrap}
.brand-dot{width:14px;height:14px;border-radius:50%;background:var(--green);flex:none}
.nav{position:absolute;left:420px;top:52px;display:flex;gap:41px;font-family:'Montserrat',sans-serif;font-weight:500;font-size:13px;color:var(--white);white-space:nowrap}
.nav .active{color:var(--green)}

/* hero */
.hero{position:absolute;left:0;top:122px;width:1200px;height:708px;background:linear-gradient(180deg,#3a2c22 0%,#5b4634 30%,#4e7a2a 60%,#7a6b58 100%)}
.hero-title{position:absolute;left:0;width:1200px;top:272px;text-align:center;font-family:'Montserrat',sans-serif;font-weight:500;font-size:58px;color:var(--white);white-space:nowrap}
.hero-sub{position:absolute;left:200px;width:800px;top:364px;text-align:center;font-family:'Montserrat',sans-serif;font-weight:500;font-size:20px;line-height:39px;color:var(--white)}
.btn-solid{position:absolute;background:var(--green);color:var(--white);border-radius:30px;font-family:'Montserrat',sans-serif;font-weight:500;text-align:center}

/* services */
.service{position:absolute;width:330px;text-align:center}
.service .photo{width:234px;height:234px;border-radius:50%;border:4px solid var(--white);margin:0 auto;box-shadow:0 0 0 1px #ddd}
.service h3{font-family:'Montserrat',sans-serif;font-weight:500;font-size:20px;margin-top:14px;color:#222}
.service p{font-size:13.5px;line-height:26px;color:var(--grey-text);margin-top:12px}
.btn-outline{display:inline-block;border:1.5px solid var(--green);color:var(--green);border-radius:24px;font-family:'Montserrat',sans-serif;font-weight:500;font-size:14px;padding:13px 24px;margin-top:16px}

/* welcome */
.welcome{position:absolute;left:0;top:1188px;width:1200px;height:555px;background:linear-gradient(90deg,#56ac2b 0%,#63a83a 38%,#9a9b72 60%,#6a8a45 100%)}
.welcome .kicker{position:absolute;left:112px;top:122px;font-family:'Montserrat',sans-serif;font-size:20px;color:var(--white)}
.welcome h2{position:absolute;left:112px;top:150px;font-family:'Montserrat',sans-serif;font-weight:500;font-size:44px;color:var(--white);white-space:nowrap}
.welcome p{position:absolute;left:112px;top:225px;width:468px;font-size:13.6px;line-height:26.6px;color:var(--white);text-align:justify}
.btn-ghost{position:absolute;left:113px;top:384px;width:166px;height:58px;border:2px solid var(--white);border-radius:30px;color:var(--white);font-family:'Montserrat',sans-serif;font-weight:500;font-size:15px;line-height:54px;text-align:center}

/* section titles */
.section-title{position:absolute;left:0;width:1200px;text-align:center;font-family:'Montserrat',sans-serif;font-weight:500;font-size:32px;color:var(--ink)}
.section-title span{color:var(--green)}
.rule{position:absolute;left:578px;width:44px;height:3px;background:var(--green)}

/* gallery */
.gallery{position:absolute;left:111px;top:1879px;width:978px;display:grid;grid-template-columns:repeat(3,317px);gap:13px}
.gallery div{height:253px}

/* testimonials */
.testimonials{position:absolute;left:0;top:2470px;width:1200px;height:542px;background:var(--soft)}
.testimonial{position:absolute;width:340px;text-align:center}
.testimonial .avatar{width:170px;height:170px;border-radius:50%;margin:0 auto}
.testimonial p{position:relative;margin-top:22px;font-size:13.5px;line-height:26px;color:var(--grey-text)}
.testimonial .name{margin-top:18px;font-family:'Montserrat',sans-serif;font-weight:500;font-size:16px;color:#333}
.quote{position:absolute;font-family:Georgia,serif;font-size:44px;color:#bbb;line-height:1}

/* contact */
.contact{position:absolute;left:0;top:3012px;width:1200px;height:521px;background:linear-gradient(180deg,#1c1b19,#2a2824 60%,#1a1917)}
.contact h2{position:absolute;left:113px;top:44px;font-family:'Montserrat',sans-serif;font-weight:400;font-size:38px;color:var(--white)}
.contact h2 b{font-weight:600}
.info{position:absolute;left:113px;color:var(--white)}
.info svg{position:absolute;left:0;top:0}
.info h4{position:absolute;left:65px;top:0;font-family:'Montserrat',sans-serif;font-weight:500;font-size:18px;white-space:nowrap}
.info span{position:absolute;left:65px;top:30px;font-size:13px;white-space:nowrap}
.field{position:absolute;border-bottom:1px solid #777;color:var(--white);font-family:'Montserrat',sans-serif;font-size:15px;padding-bottom:12px}
.social{position:absolute;left:724px;top:344px;display:flex;gap:7px}
.social i{display:block;width:36px;height:36px;border:1.5px solid var(--white);border-radius:50%}
.copyright{position:absolute;left:0;width:1200px;top:470px;text-align:center;font-size:14px;color:var(--white)}
</style>
</head>
<body>

<header class="site-header">
  <div class="brand"><span class="brand-dot"></span>BRACKWELL LANDSCAPES</div>
  <nav class="nav">
    <span class="active">HOME</span><span>ABOUT US</span><span>DRIVEWAYS</span><span>PAVING</span><span>FENCING</span><span>NEWS</span><span>CONTACT US</span>
  </nav>
</header>

<section class="hero" role="img" aria-label="Photo of a finished garden with artificial lawn, timber sleeper steps and stone patio"></section>
<h1 class="hero-title">BRACKWELL LANDSCAPES</h1>
<div class="hero-sub">SED UT PERSPICIATIS UNDE OMNIS ISTE NATUS ERROR SIT VOLUPTATEM ACCUSANTIUM DOLOREMQUE LAUDANTIU</div>
<div class="btn-solid" style="left:505px;top:455px;width:190px;height:60px;line-height:60px;font-size:17px">READ MORE</div>

<div class="service" style="left:107px;top:718px">
  <div class="photo" role="img" aria-label="Photo of a block paved driveway with gravel edging" style="background:linear-gradient(135deg,#8d8c88,#6f6e6b 55%,#b7b2a8)"></div>
  <h3>DRIVEWAYS</h3>
  <p>Sed ut perspiciatis unde omnis iste natus<br>error sit voluptatem accusantium</p>
  <span class="btn-outline">LEARN MORE</span>
</div>
<div class="service" style="left:437px;top:718px">
  <div class="photo" role="img" aria-label="Photo of a grey slate patio beside a white rendered wall" style="background:linear-gradient(180deg,#4d5a3a 0%,#cfd3d6 40%,#6d7a93 100%)"></div>
  <h3>PAVING</h3>
  <p>Sed ut perspiciatis unde omnis iste natus<br>error sit voluptatem accusantium</p>
  <span class="btn-outline">LEARN MORE</span>
</div>
<div class="service" style="left:767px;top:718px">
  <div class="photo" role="img" aria-label="Photo of a new timber panel fence above a bark border" style="background:linear-gradient(180deg,#5a7a3c 0%,#6c8a48 45%,#c59a5a 50%,#b98b4d 85%,#5a3a22 100%)"></div>
  <h3>FENCING</h3>
  <p>Sed ut perspiciatis unde omnis iste natus<br>error sit voluptatem accusantium</p>
  <span class="btn-outline">LEARN MORE</span>
</div>

<section class="welcome" role="img" aria-label="Photo of a long timber fence along a lawn, overlaid with a green gradient">
  <div class="kicker">WELCOME TO</div>
  <h2>BRACKWELL LANDSCAPES</h2>
  <p>Sed ut perspiciatis unde omnis iste natus error sit voluptatem accusantium doloremque laudantium, totam rem aperiam, eaque ipsa quae ab illo inven tore veritatis et quasi architecto beatae vitae dicta sunt explicabo. Nemo enim ipsam voluptatem quia voluptas sit aspernatur aut odit aut fugit, sed quia dolores eos qui ratione voluptatem sequi nesciunt.</p>
  <div class="btn-ghost">READ MORE</div>
</section>

<h2 class="section-title" style="top:1796px">PHOTO <span>GALLERY</span></h2>
<div class="rule" style="top:1845px"></div>
<div class="gallery">
  <div role="img" aria-label="Photo of a swimming pool surrounded by sandstone paving" style="background:linear-gradient(180deg,#7a6a52 0%,#3aa0d6 35%,#b49c86 60%,#9c8470)"></div>
  <div role="img" aria-label="Photo of a timber deck and lawn edged with sleepers" style="background:linear-gradient(180deg,#c9a56a 0%,#b38a55 30%,#2f5a1a 55%,#a07248 85%)"></div>
  <div role="img" aria-label="Photo of a sandstone patio with a circular feature" style="background:linear-gradient(180deg,#8d8a80 0%,#b9a798 45%,#a89484 80%,#4f7a2b)"></div>
  <div role="img" aria-label="Photo of a narrow garden with slate paving and raised lawn" style="background:linear-gradient(180deg,#4a7a2a 0%,#8e5a3c 40%,#7e7f7c 70%,#5c5d5a)"></div>
  <div role="img" aria-label="Photo of a grey slate patio beside a white rendered wall" style="background:linear-gradient(180deg,#3d5a2a 0%,#d4d6d6 35%,#5f6e8a 65%,#4a5570)"></div>
  <div role="img" aria-label="Photo of a block paved driveway with gravel edging" style="background:linear-gradient(180deg,#a24a3a 0%,#8a8680 35%,#6e6b66 60%,#c8c2b8)"></div>
</div>

<section class="testimonials">
  <h2 class="section-title" style="top:52px">OUR <span>TESTIMONIALS</span></h2>
  <div class="rule" style="top:96px"></div>
  <div class="testimonial" style="left:182px;top:145px">
    <div class="avatar" role="img" aria-label="Portrait photo of a smiling customer" style="background:radial-gradient(circle,#c08a6a,#5a3a2a)"></div>
    <span class="quote" style="left:-14px;top:188px">&ldquo;</span>
    <p>Sed ut perspiciatis unde omnis iste natus error sit voluptatem accusantium doloremque laudantium, totam rem aperiam ea que ipsa quae ab illo &nbsp;arch itecto beatae vitae dicta sunt explic</p>
    <span class="quote" style="left:284px;top:282px">&rdquo;</span>
    <div class="name">DALE MERCER</div>
    <svg width="70" height="12" viewBox="0 0 70 12" style="margin-top:4px">
      <g fill="none" stroke="#e8a317"><polygon points="6,1 7.5,4.5 11,4.8 8.3,7.2 9.2,11 6,9 2.8,11 3.7,7.2 1,4.8 4.5,4.5"/><polygon transform="translate(14 0)" points="6,1 7.5,4.5 11,4.8 8.3,7.2 9.2,11 6,9 2.8,11 3.7,7.2 1,4.8 4.5,4.5"/><polygon transform="translate(28 0)" points="6,1 7.5,4.5 11,4.8 8.3,7.2 9.2,11 6,9 2.8,11 3.7,7.2 1,4.8 4.5,4.5"/><polygon transform="translate(42 0)" points="6,1 7.5,4.5 11,4.8 8.3,7.2 9.2,11 6,9 2.8,11 3.7,7.2 1,4.8 4.5,4.5"/><polygon transform="translate(56 0)" points="6,1 7.5,4.5 11,4.8 8.3,7.2 9.2,11 6,9 2.8,11 3.7,7.2 1,4.8 4.5,4.5"/></g>
    </svg>
  </div>
  <div class="testimonial" style="left:695px;top:145px">
    <div class="avatar" role="img" aria-label="Portrait photo of a smiling customer" style="background:radial-gradient(circle,#c99a7a,#4a2e22)"></div>
    <span class="quote" style="left:-14px;top:188px">&ldquo;</span>
    <p>Sed ut perspiciatis unde omnis iste natus error sit voluptatem accusantium doloremque laudantium, totam rem aperiam ea que ipsa quae ab illo &nbsp;arch itecto beatae vitae dicta sunt explic</p>
    <span class="quote" style="left:284px;top:282px">&rdquo;</span>
    <div class="name">DALE MERCER</div>
    <svg width="70" height="12" viewBox="0 0 70 12" style="margin-top:4px">
      <g fill="none" stroke="#e8a317"><polygon points="6,1 7.5,4.5 11,4.8 8.3,7.2 9.2,11 6,9 2.8,11 3.7,7.2 1,4.8 4.5,4.5"/><polygon transform="translate(14 0)" points="6,1 7.5,4.5 11,4.8 8.3,7.2 9.2,11 6,9 2.8,11 3.7,7.2 1,4.8 4.5,4.5"/><polygon transform="translate(28 0)" points="6,1 7.5,4.5 11,4.8 8.3,7.2 9.2,11 6,9 2.8,11 3.7,7.2 1,4.8 4.5,4.5"/><polygon transform="translate(42 0)" points="6,1 7.5,4.5 11,4.8 8.3,7.2 9.2,11 6,9 2.8,11 3.7,7.2 1,4.8 4.5,4.5"/><polygon transform="translate(56 0)" points="6,1 7.5,4.5 11,4.8 8.3,7.2 9.2,11 6,9 2.8,11 3.7,7.2 1,4.8 4.5,4.5"/></g>
    </svg>
  </div>
</section>

<section class="contact" role="img" aria-label="Dark photo of a paved garden behind the contact details">
  <h2>CONTACT <b>US</b></h2>
  <div class="info" style="top:127px">
    <svg width="34" height="40" viewBox="0 0 34 40" fill="none" stroke="#fff" stroke-width="1.5"><path d="M17 38C17 38 4 22 4 14a13 13 0 0 1 26 0c0 8-13 24-13 24z"/><circle cx="17" cy="14" r="5"/></svg>
    <h4>ADDRESS</h4><span>#215 Lorem Ipsum dummy text Lorem</span>
  </div>
  <div class="info" style="top:240px">
    <svg width="38" height="38" viewBox="0 0 38 38" fill="none" stroke="#fff" stroke-width="1.5"><path d="M8 3l6 8-4 4c2 5 7 10 12 12l4-4 8 6-4 6C16 35 3 22 2 8z"/><path d="M22 4a12 12 0 0 1 12 12M22 9a7 7 0 0 1 7 7"/></svg>
    <h4>PHONE</h4><span>020 7946 0321</span>
  </div>
  <div class="info" style="top:331px">
    <svg width="40" height="30" viewBox="0 0 40 30" fill="none" stroke="#fff" stroke-width="1.5"><rect x="1" y="3" width="38" height="25"/><path d="M1 3l19 15L39 3M1 28l14-13M39 28L25 15"/></svg>
    <h4>EMAIL</h4><span>info@brackwelllandscapes.example.com</span>
  </div>

  <div class="field" style="left:541px;top:73px;width:230px">First Name</div>
  <div class="field" style="left:824px;top:73px;width:230px">Last Name</div>
  <div class="field" style="left:541px;top:149px;width:230px">Email</div>
  <div class="field" style="left:824px;top:149px;width:230px">Phone</div>
  <div class="field" style="left:541px;top:279px;width:513px">Message</div>

  <div class="btn-solid" style="left:540px;top:343px;width:167px;height:52px;line-height:52px;font-size:18px">SUBMIT</div>
  <div class="social"><i></i><i></i><i></i><i></i><i></i></div>

  <div class="copyright">&copy; Copyright 2020 Brackwell Landscapes.All Rights Reserved</div>
</section>

</body>
</html>
```